Business Card Design 2018 Kestrel Machining

Hello,

We need a business card design to reflect our new website we just had designed ( http://www.kestrelmachining.ca/)

We are a growing machine shop looking to grow our clientele and are hoping to update our current business card design to match our website and industry

The colours and design of our website should match to achieve what we are looking for.

I have attached a few images for reference as well as our logo and ISO 9000 needs to be apparent on the card as well

Please let me know what you have :)
Please copy marla@kestrelmachining.ca on all communication regarding this project

Thanks !!!

Industry/Entity Type

Business

Contact Information for Business Card

Company Name, employee name and title and contact details

Colors
f78f20
ffffff
00a990

Requirements
Must have
• Our logo, Iso 9000 same colours as our website http://www.kestrelmachining.ca/

```html
<!DOCTYPE html>
<html lang="en">
<head>
<meta charset="utf-8">
<title>Kestrel Machining – Business Card</title>
<link href="https://fonts.googleapis.com/css2?family=Roboto:wght@400;500;900&display=swap" rel="stylesheet">
<style>
  :root{
    --backdrop:#e6e3df;
    --paper:#f3f3f3;
    --ink:#0a0a0a;
    --teal-light:#4fd0d8;
    --teal-dark:#17939c;
    --white:#ffffff;
    --badge:#ffffff;
  }
  *{margin:0;padding:0;box-sizing:border-box}
  html,body{width:1200px;height:960px;overflow:hidden}
  body{background:var(--backdrop);font-family:"Roboto",Arial,sans-serif;position:relative}
  .card{position:absolute;width:600px;height:343px;box-shadow:0 3px 6px rgba(0,0,0,.35);overflow:hidden}
  .card-front{left:314px;top:113px;background:var(--paper)}
  .card-back{left:311px;top:472px;background:var(--ink)}
  .front-band{position:absolute;left:0;top:0;width:600px;height:343px}
  .wordmark{position:absolute;display:flex;align-items:center;gap:12px;font-weight:900;font-size:34px;letter-spacing:1px;text-transform:uppercase;white-space:nowrap}
  .wordmark .mark{width:30px;height:30px;background:var(--teal-dark)}
  .card-front .wordmark{left:126px;top:80px;color:var(--ink)}
  .card-back .wordmark{left:140px;top:145px;color:var(--white)}
  .identity{position:absolute;left:29px;top:234px;color:var(--white)}
  .identity .name{font-size:20px;font-weight:500;text-transform:uppercase}
  .identity .title{font-size:15px;font-weight:500;margin-top:2px}
  .identity .address{font-size:15px;line-height:20px;margin-top:10px}
  .contacts{position:absolute;right:28px;top:242px;list-style:none;color:var(--white);font-size:15px;text-align:right}
  .contacts li{display:flex;justify-content:flex-end;align-items:center;gap:7px;height:20px}
  .contacts svg{width:13px;height:13px;fill:var(--white)}
  .badges{position:absolute;right:28px;top:24px;display:flex;gap:14px}
  .badge{background:var(--badge);height:26px;border-radius:2px}
  .badge.cert{width:82px}
  .badge.listing{width:76px}
  .web{position:absolute;left:0;right:0;top:288px;text-align:center;color:var(--white);font-size:15px;letter-spacing:5px}
</style>
</head>
<body>
  <section class="card card-front">
    <svg class="front-band" viewBox="0 0 600 343" aria-hidden="true">
      <defs>
        <radialGradient id="bandGlow" cx="0.5" cy="0.5" r="0.7">
          <stop offset="0" stop-color="#4fd0d8"/>
          <stop offset="1" stop-color="#17939c"/>
        </radialGradient>
      </defs>
      <rect x="0" y="199" width="600" height="144" fill="url(#bandGlow)"/>
      <path d="M0 201 H62 L82 219 L102 201 H600" fill="none" stroke="#0a0a0a" stroke-width="4"/>
      <path d="M0 198 H62 L82 216 L102 198 H600 V0 H0 Z" fill="#f3f3f3"/>
      <path d="M0 200 H62 L82 218 L102 200 H600" fill="none" stroke="#0a0a0a" stroke-width="4"/>
    </svg>
    <div class="wordmark"><span class="mark"></span>Kestrel Machining</div>
    <div class="identity">
      <p class="name">Dana Whitlock</p>
      <p class="title">CEO/FOUNDER</p>
      <p class="address">2140 Larchwood Road<br>Hamilton, Ontario L8N 2K4</p>
    </div>
    <ul class="contacts">
      <li>905 218 4417 <svg viewBox="0 0 16 16"><path d="M3 1l3 3-2 2c1 2 3 4 5 5l2-2 3 3-2 3C6 15 1 10 1 3z"/></svg></li>
      <li>905 662 1083 <svg viewBox="0 0 16 16"><path d="M4 0h8v16H4zM5.5 2v10h5V2z"/></svg></li>
      <li>905 218 4420 <svg viewBox="0 0 16 16"><path d="M4 1h8v4H4zM1 6h14v6h-3v3H4v-3H1zM5 10v4h6v-4z"/></svg></li>
      <li>marla@kestrelmachining.ca <svg viewBox="0 0 16 16"><path d="M1 3h14v1L8 9 1 4zM1 6l7 5 7-5v7H1z"/></svg></li>
    </ul>
  </section>

  <section class="card card-back">
    <div class="badges">
      <span class="badge cert" role="img" aria-label="Quality certification badge"></span>
      <span class="badge listing" role="img" aria-label="Industry listing badge"></span>
    </div>
    <div class="wordmark"><span class="mark"></span>Kestrel Machining</div>
    <p class="web">www.kestrelmachining.ca</p>
  </section>
</body>
</html>
```